Website design for an Italian restaurant in Amsterdam

I need a design for a client of mine. It is for Teatro Lucerna, an Italian restaurant in Amsterdam.
We are going for a clean, modern look but we also need to realise an authentic feel.
The restaurant is located in an old movie theatre, that is where the name Teatro Lucerna comes from.
Industry/Entity Type
Italian Restaurant
Number of Pages Required
1 page
Font styles to use
Sans Serif
Colors
Designer to choose colors to be used in the design.

```html
<!DOCTYPE html>
<html lang="en">
<head>
<meta charset="utf-8">
<title>Teatro Lucerna – Italian Restaurant</title>
<link rel="stylesheet" href="https://fonts.googleapis.com/css2?family=Open+Sans:wght@400;600&family=Roboto+Condensed:wght@400;700&display=swap">
<style>
:root{
  --accent:#a6263e;
  --accent-bright:#e8435b;
  --maroon:#4a0f1c;
  --ink:#1c1c1c;
  --muted:#777;
  --header:#0b0b0b;
  --contact:#1b1818;
  --footer:#0d0d0d;
  --panel:#f2f2f2;
  --line:#bdbdbd;
  --head-font:"Roboto Condensed",sans-serif;
  --body-font:"Open Sans",sans-serif;
}
*{box-sizing:border-box;margin:0;padding:0}
html,body{width:1200px;height:3475px;overflow:hidden}
body{position:relative;font-family:var(--body-font);color:var(--ink);background:#fff}
section,header,footer{position:absolute;left:0;width:1200px}
.abs{position:absolute}

/* header */
.site-header{top:0;height:120px;background:var(--header);color:#fff}
.brand{left:111px;top:52px;display:flex;align-items:center;gap:12px}
.brand-dot{width:34px;height:34px;border-radius:50%;background:var(--accent)}
.brand-name{font-family:var(--head-font);font-size:24px;letter-spacing:.5px;line-height:1}
.brand-tag{font-size:11px;color:#aaa;margin-top:3px}
.top-phone{right:72px;top:28px;font-family:var(--head-font);font-size:20px;display:flex;align-items:center;gap:8px}
.main-nav{right:72px;top:72px;display:flex;gap:40px;font-family:var(--head-font);font-size:17px;text-transform:uppercase}
.main-nav a{color:#fff;text-decoration:none}
.main-nav a.active{color:var(--accent-bright)}

/* hero */
.hero{top:120px;height:526px;background:radial-gradient(ellipse at 50% 45%,#6b5a4c 0%,#3c2f28 45%,#1b1411 100%)}
.hero-title{left:0;width:1200px;top:205px;text-align:center;color:#fff;font-family:var(--head-font);font-size:66px;line-height:1;letter-spacing:-1px}
.hero-title span{color:var(--accent-bright)}
.hero-sub{left:0;width:1200px;top:278px;text-align:center;color:#fff;font-family:var(--head-font);font-size:46px}
.hero-arrow{top:243px}

/* welcome */
.welcome{top:646px;height:508px;background:#fff}
.plate{left:88px;top:33px;width:426px;height:426px;border-radius:50%;background:radial-gradient(circle,#c9a26a 0%,#2a2a2a 55%,#7a4d2c 70%,#b57b47 100%)}
.welcome h2{left:591px;top:116px;font-family:var(--head-font);font-weight:400;font-size:37px;text-transform:uppercase;letter-spacing:-.3px}
.welcome h2 span{color:var(--accent)}
.welcome p{left:591px;top:166px;width:486px;font-size:14.5px;line-height:25.5px;text-align:justify}
.btn{display:inline-flex;align-items:center;justify-content:center;background:var(--accent);color:#fff;border-radius:20px;font-size:14px;text-decoration:none}
.welcome .btn{left:591px;top:341px;width:111px;height:37px}

/* services */
.services{top:1154px;height:584px;background:var(--panel)}
.card{top:185px;height:294px;border:2px solid var(--line);background:#fff;text-align:center}
.card.featured{background:var(--accent);border-color:var(--accent);color:#fff;box-shadow:0 4px 10px rgba(0,0,0,.25)}
.card-photo{left:50%;margin-left:-88px;top:-97px;width:176px;height:176px;border-radius:50%;border:5px solid #fff;box-shadow:0 2px 6px rgba(0,0,0,.2)}
.card h3{left:0;right:0;top:120px;font-family:var(--body-font);font-weight:400;font-size:23px}
.card p{left:25px;right:25px;top:160px;font-size:14px;line-height:22px;color:var(--muted)}
.card.featured p{color:#fff}
.card .more{left:0;right:0;top:225px;font-size:14px;color:var(--accent)}
.card.featured .more{color:#fff}
.card .chev{left:50%;margin-left:-9px;top:248px}
.slider-arrow{top:312px;width:56px;height:56px;border-radius:50%;background:#fff;border:1px solid #ccc;display:flex;align-items:center;justify-content:center}

/* promo */
.promo{top:1738px;height:505px;background:linear-gradient(90deg,#3c0b15 0%,var(--maroon) 50%,#5a1424 100%);color:#fff}
.promo-name{left:190px;top:108px;font-family:var(--head-font);font-size:46px;text-transform:uppercase;letter-spacing:-.5px}
.promo-kind{left:190px;top:164px;font-family:var(--body-font);font-size:28px;text-transform:uppercase}
.promo-open{left:190px;top:218px;font-size:25px;text-transform:uppercase}
.hours{left:190px;top:255px;font-size:20px;line-height:34px}
.hours td{padding-right:42px}
.promo .btn{left:190px;top:340px;width:174px;height:47px;font-size:19px;border-radius:24px}
.promo-photo{left:635px;top:4px;width:452px;height:501px;background:linear-gradient(160deg,#5c4a44 0%,#2a1d1d 50%,#110c0c 100%);box-shadow:0 0 12px rgba(0,0,0,.5)}

/* blog */
.blog{top:2243px;height:602px;background:#fff}
.blog h2{left:0;width:1200px;top:105px;text-align:center;font-family:var(--head-font);font-weight:400;font-size:37px}
.post{top:190px;width:316px}
.post-photo{left:0;top:0;width:316px;height:194px;border:3px solid #e4e4e4;box-shadow:0 1px 3px rgba(0,0,0,.15)}
.date{left:5px;top:53px;width:51px;height:90px;text-align:center;color:#fff}
.date .day{display:block;background:var(--accent);font-size:21px;line-height:28px;padding-top:4px}
.date .mon{display:block;background:var(--accent);font-size:10px;line-height:14px;padding-bottom:4px}
.date .yr{display:block;background:rgba(255,255,255,.9);color:#222;font-size:14px;line-height:40px}
.post h3{left:0;top:212px;font-weight:400;font-size:19px;white-space:nowrap}
.post p{left:0;top:245px;width:316px;font-size:13.5px;line-height:21px}
.post .read{left:0;top:296px;font-size:12px;color:var(--accent)}

/* contact */
.contact{top:2845px;height:492px;background:radial-gradient(ellipse at 50% 40%,#2c2626 0%,var(--contact) 70%);color:#fff}
.contact h2{left:0;width:1200px;top:92px;text-align:center;font-family:var(--head-font);font-weight:400;font-size:36px}
.contact .lead{left:0;width:1200px;top:146px;text-align:center;font-size:16px}
.info{left:186px;display:flex;align-items:center;gap:22px;font-size:16px}
.info svg{width:20px;flex:none}
.field{left:607px;width:410px;height:40px;background:#fff;color:#666;font-size:14px;padding:11px 12px}
.submit{left:890px;top:383px;width:127px;height:40px;border:1.5px solid #fff;border-radius:20px;display:flex;align-items:center;justify-content:center;font-size:18px}

/* footer */
.site-footer{top:3337px;height:138px;background:var(--footer);color:#fff}
.social{left:475px;top:44px;display:flex;gap:8px}
.social span{width:36px;height:36px;border-radius:50%;border:1.5px solid #fff;display:block}
.copy{left:0;width:1200px;top:92px;text-align:center;font-size:13px}
</style>
</head>
<body>

<header class="site-header">
  <div class="brand abs">
    <span class="brand-dot"></span>
    <div><div class="brand-name">TEATRO LUCERNA</div><div class="brand-tag">Ristorante Italiano</div></div>
  </div>
  <div class="top-phone abs">
    <svg width="18" height="18" viewBox="0 0 24 24" fill="#fff"><path d="M6.6 10.8a15 15 0 0 0 6.6 6.6l2.2-2.2a1 1 0 0 1 1-.25 11.4 11.4 0 0 0 3.6.57 1 1 0 0 1 1 1V20a1 1 0 0 1-1 1A17 17 0 0 1 3 4a1 1 0 0 1 1-1h3.5a1 1 0 0 1 1 1c0 1.25.2 2.45.57 3.57a1 1 0 0 1-.25 1z"/></svg>
    (+31) 20 555 0188
  </div>
  <nav class="main-nav abs">
    <a class="active" href="#">Home</a><a href="#">Menu (New)</a><a href="#">Groupmenu</a><a href="#">Reservation</a><a href="#">Contact</a>
  </nav>
</header>

<section class="hero" role="img" aria-label="Photo of a candlelit dining room with laid tables">
  <div class="hero-title abs">AUTHENTIC <span>ITALIAN</span> CUISINE</div>
  <div class="hero-sub abs">Italian Restaurant</div>
  <svg class="hero-arrow abs" style="left:74px" width="16" height="26" viewBox="0 0 16 26"><path d="M13 3 3 13l10 10" fill="none" stroke="#fff" stroke-width="3"/></svg>
  <svg class="hero-arrow abs" style="left:1110px" width="16" height="26" viewBox="0 0 16 26"><path d="M3 3l10 10L3 23" fill="none" stroke="#fff" stroke-width="3"/></svg>
</section>

<section class="welcome">
  <div class="plate abs" role="img" aria-label="Photo of grilled chicken skewers on a wooden plate"></div>
  <h2 class="abs">Welcome to <span>Teatro Lucerna</span></h2>
  <p class="abs">It is a long established fact that a reader will be distracted by the readable content of a page when looking at its layout. The point of using Lorem Ipsum is that it has a more-or-less normal distribution of letters, as opposed to using 'Content here, content here', making it look like readable English. Many desktop publishing packages and web page editors now use Lorem Ipsum as their default model text, and a search</p>
  <a class="btn abs" href="#">Read More »</a>
</section>

<section class="services">
  <div class="slider-arrow abs" style="left:44px"><svg width="12" height="20" viewBox="0 0 12 20"><path d="M10 2 2 10l8 8" fill="none" stroke="#555" stroke-width="2"/></svg></div>

  <div class="card abs" style="left:104px;width:301px">
    <div class="card-photo abs" role="img" aria-label="Photo of a sliced meat dish" style="background:radial-gradient(circle,#a8714a,#e9e2da)"></div>
    <h3 class="abs">Menu</h3>
    <p class="abs">The point of using Lorem Ipsum is that it has a more-or-less normal</p>
    <div class="more abs">View More</div>
    <svg class="chev abs" width="18" height="16" viewBox="0 0 18 16"><path d="M2 2l7 6 7-6M2 8l7 6 7-6" fill="none" stroke="var(--accent)" stroke-width="2"/></svg>
  </div>

  <div class="card featured abs" style="left:452px;width:296px">
    <div class="card-photo abs" role="img" aria-label="Photo of a plate of pasta" style="background:radial-gradient(circle,#e8c468,#c99a3c)"></div>
    <h3 class="abs">Groupmenu</h3>
    <p class="abs">We serve groupmenus for reservations for 10 guests or more</p>
    <div class="more abs">View More</div>
    <svg class="chev abs" width="18" height="16" viewBox="0 0 18 16"><path d="M2 2l7 6 7-6M2 8l7 6 7-6" fill="none" stroke="#fff" stroke-width="2"/></svg>
  </div>

  <div class="card abs" style="left:792px;width:299px">
    <div class="card-photo abs" role="img" aria-label="Photo of a seafood dish" style="background:radial-gradient(circle,#8a3a2a,#2a1a16)"></div>
    <h3 class="abs">Reservation</h3>
    <p class="abs">Tables can be reserved online through our website</p>
    <div class="more abs">View More</div>
    <svg class="chev abs" width="18" height="16" viewBox="0 0 18 16"><path d="M2 2l7 6 7-6M2 8l7 6 7-6" fill="none" stroke="var(--accent)" stroke-width="2"/></svg>
  </div>

  <div class="slider-arrow abs" style="left:1098px"><svg width="12" height="20" viewBox="0 0 12 20"><path d="M2 2l8 8-8 8" fill="none" stroke="#555" stroke-width="2"/></svg></div>
</section>

<section class="promo">
  <div class="promo-name abs">Teatro Lucerna</div>
  <div class="promo-kind abs">Italian Restaurant</div>
  <div class="promo-open abs">Now open on Sundays !</div>
  <table class="hours abs"><tr><td>Tue - Sun</td><td>18:00 - 23:00</td></tr><tr><td>Mon</td><td>Closed</td></tr></table>
  <a class="btn abs" href="#">Reserve a Table</a>
  <div class="promo-photo abs" role="img" aria-label="Photo of guests celebrating with a large bottle of champagne"></div>
</section>

<section class="blog">
  <h2 class="abs">Latest Blog</h2>
  <article class="post abs" style="left:88px">
    <div class="post-photo abs" role="img" aria-label="Photo of a plated dish" style="background:linear-gradient(135deg,#3a2a22,#d8cfc6 60%,#8a6a4a)"></div>
    <div class="date abs"><span class="day">02</span><span class="mon">JUN</span><span class="yr">2018</span></div>
    <h3 class="abs">Neque porro quisquam</h3>
    <p class="abs">It has survived not only five centuries, but also the leap into electronic typesetting,</p>
    <div class="read abs">Read More »</div>
  </article>
  <article class="post abs" style="left:440px">
    <div class="post-photo abs" role="img" aria-label="Photo of guests at an evening party" style="background:linear-gradient(135deg,#1e1a1a,#6a5a52 55%,#2a2222)"></div>
    <div class="date abs"><span class="day">02</span><span class="mon">JUN</span><span class="yr">2018</span></div>
    <h3 class="abs">Dolorem ipsum quia</h3>
    <p class="abs">It has survived not only five centuries, but also the leap into electronic typesetting, remaining</p>
    <div class="read abs">Read More »</div>
  </article>
  <article class="post abs" style="left:795px">
    <div class="post-photo abs" role="img" aria-label="Photo of a bottle with a sparkler at a party" style="background:linear-gradient(135deg,#2a2218,#8a7040 50%,#1a1510)"></div>
    <div class="date abs"><span class="day">02</span><span class="mon">JUN</span><span class="yr">2018</span></div>
    <h3 class="abs">Ipsum quia dolor sit amet,</h3>
    <p class="abs">It has survived not only five centuries, but also the leap into electronic typesetting, remaining</p>
    <div class="read abs">Read More »</div>
  </article>
</section>

<section class="contact">
  <h2 class="abs">Contact us</h2>
  <div class="lead abs">Neque porro quisquam est qui dolorem ipsum quia dolor sit amet</div>
  <div class="info abs" style="top:3078px;top:233px">
    <svg viewBox="0 0 20 26" height="24"><path d="M10 1a8 8 0 0 0-8 8c0 6 8 16 8 16s8-10 8-16a8 8 0 0 0-8-8zm0 11a3 3 0 1 1 0-6 3 3 0 0 1 0 6z" fill="#fff"/></svg>
    Lindengracht 42 1015KD Amsterdam
  </div>
  <div class="info abs" style="top:287px">
    <svg viewBox="0 0 24 24" height="20"><path d="M6.6 10.8a15 15 0 0 0 6.6 6.6l2.2-2.2a1 1 0 0 1 1-.25 11.4 11.4 0 0 0 3.6.57 1 1 0 0 1 1 1V20a1 1 0 0 1-1 1A17 17 0 0 1 3 4a1 1 0 0 1 1-1h3.5a1 1 0 0 1 1 1c0 1.25.2 2.45.57 3.57a1 1 0 0 1-.25 1z" fill="#fff"/></svg>
    (+31) 20 555 0188
  </div>
  <div class="info abs" style="top:341px">
    <svg viewBox="0 0 24 18" height="16"><rect x="1" y="1" width="22" height="16" rx="2" fill="#fff"/><path d="M2 2l10 8 10-8" fill="none" stroke="#1b1818" stroke-width="2"/></svg>
    info@teatrolucerna.nl
  </div>
  <div class="field abs" style="top:223px">Name</div>
  <div class="field abs" style="top:274px">Phone</div>
  <div class="field abs" style="top:323px;height:41px">Message</div>
  <div class="submit abs">Submit</div>
</section>

<footer class="site-footer">
  <div class="social abs" aria-label="Social links"><span></span><span></span><span></span><span></span><span></span><span></span></div>
  <div class="copy abs">Copyright © 2018. All Rights Reserved</div>
</footer>

</body>
</html>
```